Stationery & Envelope Design

Executive Style looking stationery & envelope design.
Business Information:
TKL Executive Realty
2875 Birchwood Lane, Roseville, CA 95661-4180
Phone: 916.555.0142
Fax: 916.555.0187

Industry/Entity Type

Business

```html
<!DOCTYPE html>
<html lang="en">
<head>
<meta charset="utf-8">
<title>TKL Executive Realty — Stationery &amp; Envelopes</title>
<link href="https://fonts.googleapis.com/css2?family=Source+Sans+3:wght@400;600&family=Noto+Serif:wght@400&display=swap" rel="stylesheet">
<style>
  :root {
    --backdrop: #4a2c1c;
    --paper: #ffffff;
    --paper-shade: #ececec;
    --ink: #222222;
    --rule: #333333;
    --brand-blue: #1f3fae;
    --brand-blue-deep: #0f238a;
    --brand-green: #5c9a1a;
    --label: #f3f0ea;
  }
  * { box-sizing: border-box; margin: 0; padding: 0; }
  html, body { width: 1200px; height: 525px; overflow: hidden; }
  body {
    background: var(--backdrop);
    font-family: "Source Sans 3", Arial, sans-serif;
    color: var(--ink);
    position: relative;
  }
  .sheet {
    position: absolute;
    top: 13px;
    width: 354px;
    height: 457px;
    background: var(--paper);
  }
  .sheet--letterhead { left: 15px; }
  .sheet--fax { left: 382px; }

  .company-name {
    position: absolute;
    font-family: "Noto Serif", Georgia, serif;
    font-weight: 400;
    color: var(--ink);
    white-space: nowrap;
  }
  .sheet .company-name { left: 8px; top: 28px; font-size: 8px; }

  .contact {
    position: absolute;
    left: 289px;
    top: 24px;
    padding-left: 5px;
    border-left: 0.8px solid var(--rule);
    font-size: 6.2px;
    line-height: 9px;
    letter-spacing: 0.3px;
  }
  .contact span { display: flex; align-items: center; gap: 2px; }
  .contact svg { width: 5px; height: 5px; fill: var(--ink); }

  .footer-address {
    position: absolute;
    right: 7px;
    font-family: "Noto Serif", Georgia, serif;
    font-size: 7.4px;
    white-space: nowrap;
  }
  .sheet .footer-address { top: 433px; }
  .footer-rule {
    position: absolute;
    left: 59px;
    right: 0;
    height: 3px;
    background: var(--brand-blue-deep);
  }
  .sheet .footer-rule { top: 444px; }
  .footer-band {
    position: absolute;
    left: 0;
    right: 0;
    height: 8px;
    background: var(--brand-green);
  }
  .sheet .footer-band { bottom: 0; }

  .fax-title {
    position: absolute;
    left: 8px;
    top: 92px;
    font-size: 21px;
    font-weight: 400;
    letter-spacing: 0.5px;
  }
  .fax-field {
    position: absolute;
    height: 12px;
    font-size: 5.6px;
    border-bottom: 0.8px solid var(--rule);
    padding-top: 4px;
  }
  .fax-field--left { left: 7px; width: 171px; }
  .fax-field--right { left: 187px; width: 122px; }
  .fax-options {
    position: absolute;
    left: 7px;
    top: 230px;
    display: flex;
    font-size: 5.6px;
  }
  .fax-option { display: flex; align-items: center; gap: 4px; margin-right: 18px; }
  .fax-option::before {
    content: "";
    width: 7px; height: 7px;
    border: 0.8px solid var(--rule);
  }

  .option-label {
    position: absolute;
    top: 489px;
    width: 200px;
    text-align: center;
    font-size: 24px;
    color: var(--label);
  }
  .option-label--one { left: 80px; }
  .option-label--two { left: 454px; }

  .envelope {
    position: absolute;
    background: var(--paper);
    overflow: hidden;
  }
  .envelope--back-blue { left: 788px; top: 18px; width: 392px; height: 240px; }
  .envelope--back-orange {
    left: 778px; top: 96px; width: 395px; height: 178px;
    background: linear-gradient(180deg, var(--paper-shade), var(--paper));
  }
  .envelope__flap { position: absolute; left: 0; top: 0; width: 100%; }
  .flap-name {
    position: absolute;
    left: 0; width: 100%;
    text-align: center;
    font-family: "Noto Serif", Georgia, serif;
    font-size: 10px;
    font-weight: 400;
    color: var(--paper);
  }
  .envelope--back-blue .flap-name { top: 36px; }
  .envelope--back-orange .flap-name { top: 40px; }

  .envelope--front {
    left: 750px; top: 184px; width: 396px; height: 177px;
    background: linear-gradient(135deg, var(--paper) 30%, var(--paper-shade));
  }
  .envelope--front .company-name { left: 12px; top: 28px; font-size: 8px; }
  .envelope--front .footer-address { right: auto; left: 68px; top: 152px; }
  .envelope--front .footer-rule { top: 164px; }
  .envelope--front .footer-band { bottom: 0; height: 7px; }
</style>
</head>
<body>

  <section class="sheet sheet--letterhead" aria-label="Letterhead">
    <div class="company-name">TKL Executive Realty</div>
    <div class="contact">
      <span><svg viewBox="0 0 10 10"><path d="M2 0.5 L4 2.5 L3 4 Q4.5 6 6 7 L7.5 6 L9.5 8 L8 9.5 Q3 9 0.5 2 Z"/></svg>916.555.0142</span>
      <span><svg viewBox="0 0 10 10"><path d="M2 0.5 L4 2.5 L3 4 Q4.5 6 6 7 L7.5 6 L9.5 8 L8 9.5 Q3 9 0.5 2 Z"/></svg>916.555.0187</span>
    </div>
    <div class="footer-address">2875 Birchwood Lane, Roseville, CA 95661-4180</div>
    <div class="footer-rule"></div>
    <div class="footer-band"></div>
  </section>

  <section class="sheet sheet--fax" aria-label="Fax cover sheet">
    <div class="company-name">TKL Executive Realty</div>
    <div class="contact">
      <span><svg viewBox="0 0 10 10"><path d="M2 0.5 L4 2.5 L3 4 Q4.5 6 6 7 L7.5 6 L9.5 8 L8 9.5 Q3 9 0.5 2 Z"/></svg>916.555.0142</span>
      <span><svg viewBox="0 0 10 10"><path d="M2 0.5 L4 2.5 L3 4 Q4.5 6 6 7 L7.5 6 L9.5 8 L8 9.5 Q3 9 0.5 2 Z"/></svg>916.555.0187</span>
    </div>
    <h1 class="fax-title">FAX</h1>
    <div class="fax-field fax-field--left" style="top:130px">To :</div>
    <div class="fax-field fax-field--right" style="top:130px">From :</div>
    <div class="fax-field fax-field--left" style="top:149px">Fax :</div>
    <div class="fax-field fax-field--right" style="top:149px">Pages :</div>
    <div class="fax-field fax-field--left" style="top:167px">Phone :</div>
    <div class="fax-field fax-field--right" style="top:167px">Date :</div>
    <div class="fax-field fax-field--left" style="top:186px">Re :</div>
    <div class="fax-field fax-field--right" style="top:186px">CC :</div>
    <div class="fax-options">
      <span class="fax-option">Urgent</span>
      <span class="fax-option">For Review</span>
      <span class="fax-option">Please Comment</span>
      <span class="fax-option">Please Reply</span>
      <span class="fax-option">Please Recycle</span>
    </div>
    <div class="footer-address">2875 Birchwood Lane, Roseville, CA 95661-4180</div>
    <div class="footer-rule"></div>
    <div class="footer-band"></div>
  </section>

  <div class="option-label option-label--one">Option-1</div>
  <div class="option-label option-label--two">Option-2</div>

  <section class="envelope envelope--back-blue" aria-label="Envelope back, blue flap">
    <svg class="envelope__flap" viewBox="0 0 392 70" height="70" preserveAspectRatio="none">
      <defs>
        <radialGradient id="flapBlue" cx="50%" cy="30%" r="70%">
          <stop offset="0" stop-color="#2e55e0"/>
          <stop offset="1" stop-color="#0b1e8c"/>
        </radialGradient>
      </defs>
      <path d="M0 0 H392 V14 Q392 24 376 30 L216 68 Q196 72 176 68 L16 30 Q0 24 0 14 Z" fill="url(#flapBlue)"/>
    </svg>
    <div class="flap-name">TKL Executive Realty</div>
  </section>

  <section class="envelope envelope--back-orange" aria-label="Envelope back, orange flap">
    <svg class="envelope__flap" viewBox="0 0 395 70" height="70" preserveAspectRatio="none">
      <defs>
        <radialGradient id="flapOrange" cx="50%" cy="55%" r="60%">
          <stop offset="0" stop-color="#ffd21c"/>
          <stop offset="1" stop-color="#f06c08"/>
        </radialGradient>
      </defs>
      <path d="M0 0 H395 V14 Q395 24 379 30 L217 68 Q197 72 178 68 L16 30 Q0 24 0 14 Z" fill="url(#flapOrange)"/>
    </svg>
    <div class="flap-name">TKL Executive Realty</div>
  </section>

  <section class="envelope envelope--front" aria-label="Envelope front">
    <div class="company-name">TKL Executive Realty</div>
    <div class="footer-address">2875 Birchwood Lane, Roseville, CA 95661-4180</div>
    <div class="footer-rule"></div>
    <div class="footer-band"></div>
  </section>

</body>
</html>
```